Business Cards Design for the electrical wholesaler: clean bold dynamic :)

We need a business card design that would follow our latest brand guidelines. As an electrical wholesaler we want to bring a fresh look and feel into the industry. The design should be clean bold and dynamic. It should come alive with the renewed energy of our green colour. Our grey colour should keep things balanced and complement the notion of maturity and responsibility. We employ Lato as a corporate font however are not bound by this font and we’re open to interpretation here.

Target Market(s)

Electrical contractors

Industry/Entity Type

Business

Contact Information for Business Card

Logo
Name & Surname: Halyna Dorosh
Job Title: Director of Marketing
Email: halya.dorosh@quillmail.example
Cell phone: 780.555.0192
Address: 20517 - 87 Ave. Edmonton, AB, Canada. T6K 4N8
Business Phone: 780.555.0184
Website: www.brovix.example

Font styles to use
Other font styles liked:
• Lato

Requirements
Must have
• Logo & website
Nice to have
• Brand elements - some of them you may find in the attached Brand Guidelines (e.g. three lines on the background signifying "W")

```html
<!DOCTYPE html>
<html lang="en">
<head>
<meta charset="utf-8">
<title>Brovix Business Card</title>
<link href="https://fonts.googleapis.com/css2?family=Work+Sans:wght@400;500&display=swap" rel="stylesheet">
<style>
  :root {
    --backdrop: #ebe8e3;
    --card-grey: #5f5f5d;
    --panel-grey: #3f3f3e;
    --text-light: #dcd9d3;
    --text-muted: #c7c3bc;
    --brand-green: #7bb23a;
  }
  * { margin: 0; padding: 0; box-sizing: border-box; }
  html, body {
    width: 1200px;
    height: 1047px;
    overflow: hidden;
    background: var(--backdrop);
    font-family: "Work Sans", Arial, sans-serif;
  }
  .canvas {
    position: relative;
    width: 1200px;
    height: 1047px;
  }
  .business-card {
    position: absolute;
    left: 120px;
    top: 253px;
    width: 960px;
    height: 540px;
    border-radius: 24px;
    background: var(--card-grey);
    overflow: hidden;
    color: var(--text-light);
  }
  .brand-panel {
    position: absolute;
    right: 0;
    top: 0;
    width: 400px;
    height: 100%;
    background: var(--panel-grey);
  }
  .brand-band {
    position: absolute;
    right: 0;
    top: 0;
    width: 36px;
    height: 220px;
    background: var(--brand-green);
  }
  .brand-name {
    position: absolute;
    left: 52px;
    top: 52px;
    display: flex;
    align-items: center;
    gap: 14px;
    font-size: 50px;
    font-weight: 500;
    letter-spacing: -0.5px;
    color: var(--text-light);
    line-height: 1;
  }
  .brand-dot {
    width: 30px;
    height: 30px;
    border-radius: 50%;
    background: var(--brand-green);
  }
  .contact-block {
    position: absolute;
    left: 52px;
    top: 226px;
    width: 500px;
  }
  .person-name {
    font-size: 34px;
    font-weight: 500;
    letter-spacing: 0.3px;
    color: var(--text-light);
  }
  .person-role {
    margin-top: 4px;
    font-size: 21px;
    color: var(--text-muted);
    letter-spacing: 0.5px;
  }
  .address {
    margin-top: 22px;
    font-size: 21px;
    line-height: 31px;
    color: var(--text-light);
    letter-spacing: 0.6px;
  }
  .contact-list {
    margin-top: 10px;
    list-style: none;
  }
  .contact-item {
    display: flex;
    align-items: center;
    gap: 16px;
    font-size: 21px;
    line-height: 30px;
    letter-spacing: 0.6px;
    color: var(--text-light);
    white-space: nowrap;
  }
  .contact-icon {
    width: 15px;
    height: 15px;
    flex: none;
  }
  .phone-sep {
    color: var(--text-muted);
    margin: 0 4px;
  }
</style>
</head>
<body>
<main class="canvas">
  <section class="business-card" aria-label="Brovix business card">
    <div class="brand-panel"></div>
    <div class="brand-band"></div>

    <div class="brand-name">
      <span class="brand-dot"></span>
      <span>brovix</span>
    </div>

    <div class="contact-block">
      <h1 class="person-name">Halyna Dorosh</h1>
      <p class="person-role">Director of Marketing</p>
      <p class="address">20517 - 87 Ave.<br>Edmonton, AB, Canada. T6K 4N8</p>
      <ul class="contact-list">
        <li class="contact-item">
          <svg class="contact-icon" viewBox="0 0 16 16" aria-hidden="true">
            <path d="M3.5 1.5l2.5 0.5 1 3-1.6 1.2c.8 1.7 2 2.9 3.7 3.7L10.3 8.3l3 1 .5 2.5-1.8 1.8C6.8 13.2 2.8 9.2 1.7 3.3z" fill="var(--text-light)"/>
          </svg>
          <span>780.555.0184<span class="phone-sep">|</span>C 780.555.0192</span>
        </li>
        <li class="contact-item">
          <svg class="contact-icon" viewBox="0 0 16 16" aria-hidden="true">
            <rect x="1.5" y="3.5" width="13" height="9" rx="1" fill="none" stroke="var(--text-light)" stroke-width="1.4"/>
            <path d="M1.8 4l6.2 4.6L14.2 4" fill="none" stroke="var(--text-light)" stroke-width="1.4"/>
          </svg>
          <span>halya.dorosh@quillmail.example</span>
        </li>
        <li class="contact-item">
          <svg class="contact-icon" viewBox="0 0 16 16" aria-hidden="true">
            <circle cx="8" cy="8" r="6.3" fill="none" stroke="var(--text-light)" stroke-width="1.3"/>
            <ellipse cx="8" cy="8" rx="2.7" ry="6.3" fill="none" stroke="var(--text-light)" stroke-width="1.1"/>
            <path d="M1.8 8h12.4M2.8 4.8h10.4M2.8 11.2h10.4" stroke="var(--text-light)" stroke-width="1.1"/>
          </svg>
          <span>www.brovix.example</span>
        </li>
      </ul>
    </div>
  </section>
</main>
</body>
</html>
```